Window and GutterCleaning Flyer A5 size double sided.

We need a double sided A5 flyer. Side 1, is for window cleaning, side 2 is for gutter cleaning. Licensed by Borough of Marlow Council.
Phone number 0800 473 1926.
Business address 17 Fallowmere Close, North Brack Edinburgh EH31 4LP.
www.clearpane-hub-services.com
We use a LoftEye Gutter inspection Cam to view your gutters first to see if they need doing.
Window cleaning ; Professional window cleaning services, what we offer, water fed pole window cleaning able to reach windows up to 60 feet.
Conservatory cleaning.
Conservatory roof cleaning.
Fascias & Soffits cleaning.
Excellent Customer Service.
Target Market(s)
domestic houses
Industry/Entity Type
window cleaning
Look and feel
Each slider illustrates characteristics of the customer's brand and the style your logo design should communicate.

```html
<!DOCTYPE html>
<html lang="en">
<head>
<meta charset="utf-8">
<title>ClearPane Hub – Window &amp; Gutter Flyer</title>
<link href="https://fonts.googleapis.com/css2?family=Poppins:wght@400;500;600;700;800&family=Oswald:wght@500;600&display=swap" rel="stylesheet">
<style>
:root{
  --navy:#2b2560;
  --navy-deep:#231e55;
  --sky:#6aaee8;
  --sky-pale:#a9d0f2;
  --tile-a:#5b66a3;
  --tile-b:#38347e;
  --ink:#222;
  --backdrop:#c8c8c8;
  --white:#fff;
}
*{box-sizing:border-box;margin:0;padding:0}
html,body{width:1200px;height:1200px;overflow:hidden;background:var(--backdrop);font-family:'Poppins',sans-serif;color:var(--ink)}
.page{position:absolute;top:230px;width:520px;height:738px;background:var(--white);overflow:hidden}
.page--windows{left:55px}
.page--gutters{left:618px}
.abs{position:absolute}
.brand{display:flex;align-items:center;gap:6px;font-weight:700;color:var(--navy);font-size:17px;white-space:nowrap}
.brand__mark{width:12px;height:12px;background:var(--sky)}
.photo{position:absolute;border-radius:3px;box-shadow:0 1px 4px rgba(0,0,0,.25)}
.band{position:absolute;left:0;width:520px}
.band svg{display:block}
.section-title{position:absolute;color:var(--white);font-weight:700;font-size:20px;letter-spacing:.5px;display:flex;align-items:center;gap:8px}
.rule{height:1px;background:rgba(255,255,255,.7)}
.offer{position:absolute;height:35px;border-radius:4px;display:flex;align-items:center;padding-left:14px;color:var(--white);font-size:8.6px;line-height:1.2}
.offer--a{background:var(--tile-a)}
.offer--b{background:var(--tile-b)}
.offer__icon{position:absolute;left:-12px;top:6px;width:23px;height:23px;border-radius:50%;background:var(--white);border:2px solid var(--sky-pale);display:flex;align-items:center;justify-content:center}
.offer__icon svg{width:11px;height:11px}
.footer-quote{font-size:10.5px;line-height:1.35;color:var(--ink)}
.footer-quote b{color:var(--navy)}
.pill{position:absolute;height:18px;border-radius:9px;background:var(--navy);color:var(--white);font-size:10px;display:flex;align-items:center;justify-content:center}
.hl-navy{color:var(--navy)}
.hl-sky{color:var(--sky)}
.arrow-tag{position:absolute;color:var(--white);font-weight:600;font-size:20px;display:flex;align-items:center}
.why li{list-style:none;display:flex;gap:6px;font-size:11.5px;line-height:1.05;margin-bottom:9px;color:var(--ink)}
.why svg{flex:none;width:11px;height:11px;margin-top:1px}
</style>
</head>
<body>

<!-- Side 1: windows -->
<section class="page page--windows">
  <div class="abs brand" style="left:72px;top:62px"><span class="brand__mark"></span>ClearPane Hub</div>

  <div class="abs" style="left:0;width:266px;top:128px;text-align:center;line-height:1">
    <div style="font-size:17px;letter-spacing:.8px">Let the Sunshine In</div>
    <div style="font-size:24px;font-weight:500;margin-top:4px">Sparkling <span class="hl-sky">✦</span></div>
    <div class="hl-navy" style="font-size:37px;font-weight:800;margin-top:3px">Windows</div>
    <div class="hl-sky" style="font-size:36px;font-weight:800;margin-top:-2px">Guaranteed</div>
  </div>

  <div class="abs" style="left:253px;top:24px;width:248px;height:211px;background:#3f4a6e;padding:4px;display:flex;gap:4px">
    <div role="img" aria-label="Squeegee cleaning wet window glass" style="flex:1;background:linear-gradient(160deg,#5e7fa8,#c9d7e6 60%,#8fa6c2)"></div>
    <div role="img" aria-label="Red brick house with white windows" style="flex:1;background:linear-gradient(180deg,#b9c6d4,#8c4a36 45%,#a86a52)"></div>
    <div role="img" aria-label="Water-fed pole brush on window" style="flex:1;background:linear-gradient(170deg,#8ea0b4,#e9edf1 50%,#b8c2cc)"></div>
  </div>

  <p class="abs" style="left:35px;top:249px;width:455px;font-size:9.6px;line-height:1.25">We offer high-quality window cleaning for homes and businesses, delivering. We only clean domestic properties not businesses. Spotless, streak-free results every time. As per last info, can't claim this too.</p>

  <div class="band" style="top:290px">
    <svg width="520" height="163" viewBox="0 0 520 163" preserveAspectRatio="none">
      <path d="M0 10 C60 0 90 12 160 8 C230 4 250 -2 310 6 C380 14 440 2 520 10 L520 163 L0 163Z" fill="var(--navy)"/>
      <path d="M0 4 C60 -4 100 10 160 4" stroke="var(--navy)" stroke-width="1.5" fill="none"/>
    </svg>
  </div>
  <div class="section-title" style="left:80px;top:318px"><span class="rule" style="width:122px"></span>WE OFFER<span class="rule" style="width:122px"></span></div>

  <div class="offer offer--a" style="left:41px;top:352px;width:134px">Water-Fed Pole Cleaning<br>– Up to 60 Feet<span class="offer__icon"><svg viewBox="0 0 12 12"><path d="M2 10 L10 2" stroke="var(--navy)" stroke-width="1.5"/></svg></span></div>
  <div class="offer offer--a" style="left:201px;top:352px;width:134px">Fascia &amp; Soffit Cleaning<span class="offer__icon"><svg viewBox="0 0 12 12"><rect x="2" y="3" width="8" height="6" fill="none" stroke="var(--navy)" stroke-width="1.3"/></svg></span></div>
  <div class="offer offer--b" style="left:358px;top:352px;width:134px">Reliable, Friendly Service<span class="offer__icon"><svg viewBox="0 0 12 12"><circle cx="6" cy="6" r="4" fill="none" stroke="var(--navy)" stroke-width="1.3"/></svg></span></div>
  <div class="offer offer--a" style="left:41px;top:395px;width:134px">Conservatory<br>Windows &amp; Roofs<span class="offer__icon"><svg viewBox="0 0 12 12"><rect x="3" y="2" width="6" height="8" fill="none" stroke="var(--navy)" stroke-width="1.3"/></svg></span></div>
  <div class="offer offer--b" style="left:201px;top:395px;width:134px">One-off or Regular<br>Cleans<span class="offer__icon"><svg viewBox="0 0 12 12"><path d="M6 1v10M1 6h10" stroke="var(--navy)" stroke-width="1.3"/></svg></span></div>
  <div class="offer offer--a" style="left:358px;top:395px;width:134px;flex-direction:column;align-items:flex-start;justify-content:center">Licensed by<span style="display:block;width:84px;height:12px;margin-top:3px;border:1px solid var(--white);border-radius:2px"></span><span class="offer__icon"><svg viewBox="0 0 12 12"><path d="M2 6l3 3 5-6" stroke="var(--navy)" stroke-width="1.5" fill="none"/></svg></span></div>

  <div class="photo" role="img" aria-label="Rope access cleaner on glass building" style="left:32px;top:472px;width:108px;height:89px;background:linear-gradient(160deg,#dfe9f2,#8fb3d6)"></div>
  <div class="photo" role="img" aria-label="Rugged inspection camera monitor" style="left:152px;top:472px;width:109px;height:89px;background:radial-gradient(circle at 50% 55%,#5c5d60,#e3e3e3 60%);box-shadow:none"></div>
  <div class="photo" role="img" aria-label="Cleaners abseiling down blue glass tower" style="left:32px;top:575px;width:108px;height:89px;background:linear-gradient(170deg,#9fb7d4,#3e7fc4)"></div>
  <div class="photo" role="img" aria-label="White conservatory on brick house" style="left:152px;top:575px;width:109px;height:89px;background:linear-gradient(180deg,#a65a3f,#efefef 45%,#c8a58f)"></div>

  <div class="abs" style="left:288px;top:476px;line-height:1.15">
    <div style="font-size:18px;font-weight:500">GREAT SERVICE FROM</div>
    <div class="hl-navy" style="font-size:18px;font-weight:700">START TO FINISH</div>
    <div style="font-size:15.2px;font-weight:600;line-height:1.2;margin-top:5px;width:205px">Reliable, professional and the windows have never looked better!</div>
  </div>
  <div class="abs" style="left:290px;top:590px;width:199px;height:1px;background:#999"></div>
  <div class="abs" style="left:289px;top:602px;font-size:17.5px;white-space:nowrap">BASED IN <b class="hl-navy">NORTH BRACK</b></div>
  <div class="abs" style="left:290px;top:629px;width:199px;height:34px;background:var(--sky-pale);border-radius:4px;display:flex;align-items:center;justify-content:center;font-size:15.5px;color:var(--navy-deep)">Serving All of Edinburgh</div>

  <div class="abs footer-quote" style="left:33px;top:685px">Get a <b>FREE QUOTE</b><br><span class="hl-navy">✆</span> 0800 473 1926</div>
  <div class="abs footer-quote" style="left:147px;top:685px;display:flex;gap:4px"><svg width="8" height="11" viewBox="0 0 8 11"><path d="M4 11C1 7 0 5 0 4a4 4 0 018 0c0 1-1 3-4 7z" fill="var(--navy)"/><circle cx="4" cy="4" r="1.5" fill="#fff"/></svg><span>17 Fallowmere Close, North<br>Brack, Edinburgh EH31 4LP</span></div>
  <div class="pill" style="left:300px;top:688px;width:195px;font-size:9.8px">www.clearpane-hub-services.com</div>
</section>

<!-- Side 2: gutters -->
<section class="page page--gutters">
  <div class="abs brand" style="left:110px;top:50px"><span class="brand__mark"></span>ClearPane Hub</div>

  <div role="img" aria-label="Roofline with white gutter, fascia and soffit on brick house" class="abs" style="left:260px;top:35px;width:260px;height:250px;clip-path:polygon(100% 0,100% 100%,10% 100%,20% 78%);background:linear-gradient(200deg,#f2f4f6,#c9ced4 45%,#8a5a48 80%,#a77760)"></div>

  <div class="abs" style="left:30px;top:110px;line-height:1">
    <div style="font-size:23.5px;font-weight:500;letter-spacing:.8px">Don’t Let Blocked</div>
    <div class="hl-sky" style="font-size:32px;font-weight:700;margin-top:2px">Gutters Cause</div>
    <div class="hl-navy" style="font-size:32px;font-weight:700;margin-top:0">Costly Damage</div>
    <div style="font-size:18px;font-weight:500;line-height:1.2;margin-top:6px">We inspect before<br>we clean saving you time<br>and money.</div>
  </div>

  <svg class="abs" style="left:275px;top:55px" width="215" height="195" viewBox="0 0 215 195">
    <polygon points="83,6 180,6 180,0 211,25 180,50 180,44 83,44 95,25" fill="var(--navy)"/>
    <polygon points="43,72 140,72 140,66 171,91 140,116 140,110 43,110 55,91" fill="var(--sky)"/>
    <polygon points="4,148 102,148 102,142 133,167 102,192 102,186 4,186 16,167" fill="var(--navy)"/>
  </svg>
  <div class="arrow-tag" style="left:385px;top:64px">Gutter</div>
  <div class="arrow-tag" style="left:344px;top:131px">Fascia</div>
  <div class="arrow-tag" style="left:305px;top:208px">Soffit</div>

  <div class="band" style="top:265px">
    <svg width="520" height="173" viewBox="0 0 520 173" preserveAspectRatio="none">
      <path d="M0 10 C70 2 120 6 180 4 C250 2 300 0 340 6 C420 16 470 8 520 4 L520 173 L0 173Z" fill="var(--navy)"/>
    </svg>
  </div>

  <div class="abs" style="left:34px;top:302px;width:127px;height:113px;background:#2f7fcc;border-radius:6px;padding:3px">
    <div style="border:1px dashed rgba(255,255,255,.8);border-radius:4px;height:100%;overflow:hidden;text-align:center;color:var(--white)">
      <div style="font-family:'Oswald',sans-serif;font-weight:600;font-size:14px;margin-top:8px;line-height:1">FREE GUTTER CHECK</div>
      <div style="font-size:12px;line-height:1.1;margin-top:1px">with LoftEye<br>Inspection Cam</div>
      <div style="background:var(--sky);color:var(--navy-deep);font-size:7.2px;line-height:1.2;padding:5px 5px;margin-top:8px;height:50px">We show you what’s really going on before recommending service.</div>
    </div>
  </div>

  <div class="section-title" style="left:181px;top:297px">WE OFFER<span class="rule" style="width:122px"></span></div>

  <div class="offer offer--a" style="left:187px;top:332px;width:134px">Safe, No-Ladder<br>Cleaning<span class="offer__icon"><svg viewBox="0 0 12 12"><path d="M6 1l4 2v3c0 3-2 4-4 5-2-1-4-2-4-5V3z" fill="none" stroke="var(--navy)" stroke-width="1.2"/></svg></span></div>
  <div class="offer offer--a" style="left:348px;top:332px;width:134px">Prevents Overflow, Damp<br>&amp; Water Damage<span class="offer__icon"><svg viewBox="0 0 12 12"><path d="M6 1C4 5 3 6 3 8a3 3 0 006 0c0-2-1-3-3-7z" fill="none" stroke="var(--navy)" stroke-width="1.2"/></svg></span></div>
  <div class="offer offer--a" style="left:187px;top:378px;width:134px">Removes Moss, Leaves<br>&amp; Debris<span class="offer__icon"><svg viewBox="0 0 12 12"><path d="M2 10C2 4 6 2 10 2 10 7 7 10 2 10z" fill="none" stroke="var(--navy)" stroke-width="1.2"/></svg></span></div>
  <div class="offer offer--b" style="left:348px;top:378px;width:134px">Fast, Clean &amp; Fully<br>Insured<span class="offer__icon"><svg viewBox="0 0 12 12"><path d="M2 6l3 3 5-6" stroke="var(--navy)" stroke-width="1.5" fill="none"/></svg></span></div>

  <div class="photo" role="img" aria-label="Worker in hi-vis vest by conservatory" style="left:32px;top:461px;width:108px;height:89px;background:linear-gradient(180deg,#c9d3dc,#8a4f3c 45%,#d0c8b8)"></div>
  <div class="photo" role="img" aria-label="Gutter vacuum hose clearing debris" style="left:152px;top:461px;width:108px;height:89px;background:linear-gradient(150deg,#e8e8e8,#9aa0a6 50%,#2c3f9a)"></div>
  <div class="photo" role="img" aria-label="Mossy conservatory roof panels" style="left:32px;top:563px;width:108px;height:89px;background:linear-gradient(170deg,#9a8f88,#d8dad8 40%,#7f8266)"></div>
  <div class="photo" role="img" aria-label="Inspection camera on pole in garden" style="left:152px;top:563px;width:108px;height:89px;background:linear-gradient(180deg,#8b9474,#5f7a45 60%,#7d8f5a)"></div>

  <div class="abs hl-navy" style="left:283px;top:456px;font-size:17px;font-weight:700">WHY CHOOSE US?</div>
  <ul class="abs why" style="left:285px;top:481px;width:200px">
    <li><svg viewBox="0 0 12 12"><path d="M1 6L6 1l5 5M3 5v6h6V5" fill="none" stroke="var(--navy)" stroke-width="1.3"/></svg><span>Friendly, professional<br>service</span></li>
    <li><svg viewBox="0 0 12 12"><path d="M1 6L6 1l5 5M3 5v6h6V5" fill="none" stroke="var(--navy)" stroke-width="1.3"/></svg><span>Reliable and efficient</span></li>
    <li><svg viewBox="0 0 12 12"><path d="M1 6L6 1l5 5M3 5v6h6V5" fill="none" stroke="var(--navy)" stroke-width="1.3"/></svg><span>Fully licensed and insured</span></li>
    <li><svg viewBox="0 0 12 12"><path d="M1 6L6 1l5 5M3 5v6h6V5" fill="none" stroke="var(--navy)" stroke-width="1.3"/></svg><span>Excellent customer<br>satisfaction</span></li>
  </ul>
  <div class="abs" style="left:287px;top:595px;width:195px;height:1px;background:#999"></div>
  <div class="abs" style="left:286px;top:605px;font-size:14px">Stay Ahead of Leaks</div>
  <div class="abs hl-navy" style="left:286px;top:620px;display:flex;align-items:center;gap:5px">
    <span style="font-size:32px;font-weight:800;line-height:1">BOOK</span>
    <span style="font-size:13px;font-weight:700;line-height:1.05;color:var(--navy-deep)">Your Gutter<br>Check Today!</span>
  </div>

  <div class="abs footer-quote" style="left:33px;top:685px">Get a <b>FREE QUOTE</b><br><span class="hl-navy">✆</span> 0800 473 1926</div>
  <div class="pill" style="left:142px;top:688px;width:195px;font-size:9.8px">www.clearpane-hub-services.com</div>
  <div class="pill" style="left:343px;top:688px;width:68px;height:16px;background:var(--sky);color:var(--navy-deep);font-size:8.5px">Licensed by</div>
  <div class="abs" style="left:418px;top:686px;width:62px;height:20px;border:1px solid #555;border-radius:2px"></div>
</section>

</body>
</html>
```